We need a new business card that reflects who we are. Professional, classy, modern, and service ori

We need a business card design for a window coverings design company in Kansas City called Bright Lane Interiors. We offer professional, modern, and high quality window covering products. We are looking to portray an image of a big, national franchise. We are a 5 location (with showrooms) business with 10 professional designers and 4 professional installers. These cards will be used with Thank you cards, given to realtors, and asked for referrals with.

Target Market(s)

Kansas City

Industry/Entity Type

Business

Contact Information for Business Card

We would like our card to look clean and simple on the front, featuring our logo and Marlow Fenwick's. Our designers' phone numbers and emails should be displayed as well as their title.

Font styles to use
Sans Serif

Colors

Designer to choose colors to be used in the design.

Requirements
Must have
• Front - Logos, name, phone number, email address
• Back - Showroom locations, social media? Appt date/time?
Nice to have
• I would like a clean and modern look (not contemporary. I like a white background, but I am open to ideas. Looking for a "National chain" look for a small business.
Should not have
• Too much busyness.

```html
<!DOCTYPE html>
<html lang="en">
<head>
<meta charset="utf-8">
<title>Bright Lane Interiors – Business Card</title>
<link rel="stylesheet" href="https://fonts.googleapis.com/css2?family=Roboto:wght@400;500;700&family=Roboto+Condensed:wght@400;700&display=swap">
<style>
  :root {
    --backdrop: #2a2a2a;
    --card: #f3f3f3;
    --panel-grey: #8d9194;
    --brand-red: #c64045;
    --ink: #111111;
    --ink-soft: #555555;
    --line-dots: #8a8a8a;
    --white: #ffffff;
  }
  * { margin: 0; padding: 0; box-sizing: border-box; }
  html, body {
    width: 1200px; height: 960px; overflow: hidden;
    background: var(--backdrop);
    font-family: "Roboto", Arial, sans-serif;
  }
  .stage { position: relative; width: 1200px; height: 960px; }

  .card {
    position: absolute; width: 600px; height: 343px;
    background: var(--card);
    box-shadow: 0 2px 6px rgba(0,0,0,.5);
  }
  .card--front { left: 314px; top: 113px; }
  .card--back  { left: 311px; top: 472px; }

  /* Front */
  .contact-panel {
    position: absolute; left: 0; top: 29px; width: 379px; height: 286px;
    background: var(--panel-grey);
  }
  .accent-band {
    position: absolute; left: 255px; top: 0; width: 82px; height: 100%;
    background: var(--brand-red);
  }
  .designer-name {
    position: absolute; left: 27px; top: 85px;
    color: var(--brand-red); font-weight: 500; font-size: 23px; letter-spacing: .2px;
  }
  .designer-title {
    position: absolute; left: 27px; top: 111px;
    color: var(--ink); font-weight: 500; font-size: 15px;
  }
  .contact-list {
    position: absolute; left: 27px; top: 148px; list-style: none;
    color: var(--white); font-size: 14.5px; line-height: 19.5px;
  }

  .brand-mark {
    position: absolute; left: 370px; top: 110px; width: 250px; height: 120px;
    transform: rotate(-90deg);
    display: flex; flex-direction: column; align-items: center; justify-content: center;
  }
  .brand-mark__square {
    width: 46px; height: 46px; background: var(--brand-red); margin-bottom: 14px;
  }
  .brand-mark__name {
    font-size: 24px; font-weight: 400; color: var(--ink); line-height: 1.1;
  }
  .brand-mark__tagline {
    font-size: 11.5px; color: var(--ink); margin-top: 3px;
  }

  /* Back */
  .partner-name {
    position: absolute; left: 0; right: 0; top: 41px;
    display: flex; justify-content: center; align-items: center; gap: 6px;
    font-size: 15px; font-weight: 500; color: var(--ink-soft);
  }
  .partner-name__square { width: 14px; height: 14px; background: var(--panel-grey); }

  .appointment {
    position: absolute; left: 82px; width: 450px;
    display: flex; align-items: baseline;
    color: var(--brand-red); font-size: 17px;
  }
  .appointment__label { white-space: pre; }
  .appointment__fill {
    border-bottom: 1px dotted var(--line-dots); height: 1px; align-self: flex-end;
    margin-bottom: 5px;
  }
  .appointment__fill--date { width: 167px; margin-left: 5px; margin-right: 3px; }
  .appointment__fill--time { width: 106px; margin-left: 5px; margin-right: 4px; }
  .appointment__meridiem { font-size: 13.5px; }
  .appointment:nth-of-type(2) { top: 82px; }
  .appointment:nth-of-type(3) { top: 128px; }
  .appointment:nth-of-type(4) { top: 172px; }
  .appointment:nth-of-type(5) { top: 218px; }

  .showrooms {
    position: absolute; left: 0; right: 0; top: 260px; text-align: center;
    font-family: "Roboto Condensed", Arial, sans-serif;
  }
  .showrooms__heading {
    color: var(--brand-red); font-weight: 700; font-size: 15px; letter-spacing: .3px;
  }
  .showrooms__list {
    color: var(--ink-soft); font-size: 13.5px; margin-top: 4px; letter-spacing: .2px;
  }
  .social-links {
    position: absolute; left: 0; right: 0; top: 303px;
    display: flex; justify-content: center; gap: 3px;
  }
  .social-links__dot {
    width: 20px; height: 20px; border-radius: 50%; background: var(--brand-red);
  }
</style>
</head>
<body>
<main class="stage">

  <section class="card card--front" aria-label="Business card front">
    <div class="contact-panel">
      <div class="accent-band"></div>
      <h1 class="designer-name">JANE PORTER</h1>
      <p class="designer-title">DESIGNER</p>
      <ul class="contact-list">
        <li>913.555.0148</li>
        <li>info@brightlaneinteriors.com</li>
        <li>brightlaneinteriors.com</li>
      </ul>
    </div>
    <div class="brand-mark">
      <div class="brand-mark__square"></div>
      <div class="brand-mark__name">Bright Lane Interiors</div>
      <div class="brand-mark__tagline">Blinds, Shades, Shutters, Draperies &amp; Decor</div>
    </div>
  </section>

  <section class="card card--back" aria-label="Business card back">
    <div class="partner-name"><span class="partner-name__square"></span>Marlow Fenwick Gallery</div>

    <div class="appointment"><span class="appointment__label">Date :</span><span class="appointment__fill appointment__fill--date"></span><span class="appointment__label">Time :</span><span class="appointment__fill appointment__fill--time"></span><span class="appointment__meridiem">AM/PM</span></div>
    <div class="appointment"><span class="appointment__label">Date :</span><span class="appointment__fill appointment__fill--date"></span><span class="appointment__label">Time :</span><span class="appointment__fill appointment__fill--time"></span><span class="appointment__meridiem">AM/PM</span></div>
    <div class="appointment"><span class="appointment__label">Date :</span><span class="appointment__fill appointment__fill--date"></span><span class="appointment__label">Time :</span><span class="appointment__fill appointment__fill--time"></span><span class="appointment__meridiem">AM/PM</span></div>
    <div class="appointment"><span class="appointment__label">Date :</span><span class="appointment__fill appointment__fill--date"></span><span class="appointment__label">Time :</span><span class="appointment__fill appointment__fill--time"></span><span class="appointment__meridiem">AM/PM</span></div>

    <div class="showrooms">
      <h2 class="showrooms__heading">SHOWROOM LOCATIONS</h2>
      <p class="showrooms__list">ASHFORD | BRIARWOOD PARK | LAKEMONT | NORTH HAVEN | ELM CROSSING</p>
    </div>
    <div class="social-links" aria-label="Social media links">
      <span class="social-links__dot"></span>
      <span class="social-links__dot"></span>
      <span class="social-links__dot"></span>
      <span class="social-links__dot"></span>
    </div>
  </section>

</main>
</body>
</html>
```